Envelope Design - Winner can do follow-up business

- Varnoko.com is a Swiss-based online store selling business shirts and accessories for business men
- Please visit the webpage to make yourself familiar with the company. Although the text is in German, with Plimbo translator you should be able to understand the main content.
- Our clients are mainly business men between 30 and 60 years old. Mostly with a high income working in the service industry (banking, insurance, lawyers, etc.). Sometimes there wives purchase the shirts for them ;-)
- The colors and the logo are given, as they are also used for the print materials (please see files in attachment)
- I am running several businesses and often need a talented web designer --> the winner gets substantial follow-up business
your task:
-for our company we need a new envelope design
-It should be simple and modern
-please use one of the logos in the followings.
-suprise me :)

```html
<!DOCTYPE html>
<html lang="en">
<head>
<meta charset="utf-8">
<title>Varnoko Envelope Design</title>
<link rel="stylesheet" href="https://fonts.googleapis.com/css2?family=Roboto+Slab:wght@400;600&display=swap">
<style>
  :root {
    --backdrop: #dcd8d3;
    --paper: #ffffff;
    --paper-shade: #f1f1f3;
    --brand-red: #ef2e24;
    --brand-black: #000000;
    --brand-yellow: #e5d66a;
    --muted-gold: #a59a74;
    --soft-red: #f6694f;
    --ink: #111111;
    --edge: #9a9a9a;
  }
  html, body {
    margin: 0;
    padding: 0;
    overflow: hidden;
  }
  body {
    width: 1200px;
    height: 942px;
    background: var(--backdrop);
    position: relative;
    font-family: "Roboto Slab", Georgia, serif;
  }
  .envelope {
    position: absolute;
    width: 974px;
    height: 458px;
    background: var(--paper);
    box-shadow: 0 0 0 1px var(--edge);
    overflow: hidden;
  }
  .envelope--red-back { left: 208px; top: 40px; }
  .envelope--black-back {
    left: 117px; top: 229px;
    background: linear-gradient(160deg, var(--paper-shade), var(--paper));
  }
  .envelope--front { left: 35px; top: 462px; }

  .flap {
    position: absolute;
    left: 0; top: 0;
    width: 974px;
    height: 160px;
  }
  .flap-name {
    position: absolute;
    left: 0; width: 974px;
    top: 52px;
    text-align: center;
    font-weight: 600;
    font-size: 26px;
    letter-spacing: 4px;
  }
  .envelope--red-back .flap-name { color: var(--soft-red); }
  .envelope--black-back .flap-name { color: var(--muted-gold); }

  .sender-name {
    position: absolute;
    left: 18px; top: 66px;
    margin: 0;
    font-weight: 600;
    font-size: 34px;
    letter-spacing: 3px;
    color: var(--brand-yellow);
  }
  .sender-address {
    position: absolute;
    left: 22px; top: 121px;
    display: flex;
    gap: 12px;
    font-size: 20px;
    line-height: 25px;
    color: var(--ink);
  }
  .sender-address svg { margin-top: 2px; }
  .footer-rule {
    position: absolute;
    left: 0; top: 396px;
    width: 974px; height: 4px;
    background: var(--brand-red);
  }
  .footer-band {
    position: absolute;
    left: 0; top: 403px;
    width: 974px; height: 55px;
    background: var(--brand-black);
    display: flex;
    align-items: center;
    gap: 12px;
    padding-left: 26px;
    box-sizing: border-box;
  }
  .footer-url {
    color: var(--brand-yellow);
    font-size: 19px;
  }
  .footer-notch {
    position: absolute;
    left: 838px; top: 388px;
  }
</style>
</head>
<body>

  <section class="envelope envelope--red-back" aria-label="Envelope back, red flap">
    <svg class="flap" viewBox="0 0 974 160" aria-hidden="true">
      <path d="M0 0 H974 C960 30 958 68 915 78 L560 146 Q487 158 414 146 L59 78 C16 68 14 30 0 0Z" fill="var(--brand-red)"/>
    </svg>
    <div class="flap-name">VARNOKO</div>
  </section>

  <section class="envelope envelope--black-back" aria-label="Envelope back, black flap">
    <svg class="flap" viewBox="0 0 974 160" aria-hidden="true">
      <path d="M0 0 H974 C960 30 958 68 915 78 L560 146 Q487 158 414 146 L59 78 C16 68 14 30 0 0Z" fill="var(--brand-black)"/>
    </svg>
    <div class="flap-name">VARNOKO</div>
  </section>

  <section class="envelope envelope--front" aria-label="Envelope front">
    <h1 class="sender-name">VARNOKO</h1>
    <div class="sender-address">
      <svg width="18" height="24" viewBox="0 0 18 24" aria-hidden="true">
        <path d="M9 0 C4 0 0 4 0 9 C0 15 9 24 9 24 C9 24 18 15 18 9 C18 4 14 0 9 0Z" fill="var(--brand-red)"/>
        <circle cx="9" cy="9" r="3.5" fill="var(--paper)"/>
      </svg>
      <address style="font-style: normal;">Street Name, City Name<br>State Zipcode</address>
    </div>

    <div class="footer-rule"></div>
    <div class="footer-band">
      <svg width="22" height="22" viewBox="0 0 22 22" aria-hidden="true" fill="none" stroke="var(--brand-red)" stroke-width="1.6">
        <circle cx="11" cy="11" r="9.5"/>
        <ellipse cx="11" cy="11" rx="4.2" ry="9.5"/>
        <line x1="1.5" y1="11" x2="20.5" y2="11"/>
        <path d="M3 6 H19 M3 16 H19"/>
      </svg>
      <span class="footer-url">www.varnoko.com</span>
    </div>
    <svg class="footer-notch" width="104" height="56" viewBox="0 0 104 56" aria-hidden="true">
      <path d="M0 0 H104 V40 L52 54 L0 40Z" fill="var(--paper)"/>
    </svg>
  </section>

</body>
</html>
```